Greeting Card Design - Bright Hearts Open Pages

Hi there

Thank you for taking the time to read about this project.

The project is for a range of greeting cards for the gay and lesbian community. The brand is called "Bright Hearts Open Pages".

In this project I require four designs in total (designs for homosexual couples, two for men and two for women). The designs need to reflect the general concept of being in love.

I am looking for variety (fun and funky, as well as modern and classy - please design to your tastes and I will give feedback).

I will work with each designer closely and provide the words for the cards as the designs are developed.

Thank you for considering this project.
Updates

I'm currently having issues with the craft huddle website and it won't let me upload files to show the logo. I will do so as soon as the website allows me. Thanks

Target Market(s)

Gay and lesbian community.

Industry/Entity Type

Community

Requirements
Must have
• I am looking for variety in the range. I would like designs that are modern and classy range; and also designs that are fun and funky.
Nice to have
• Hand drawings are good for the fun range, so is colour.
The classy range can be symbolic (e.g. holding hands) or black and whites.
Should not have
• Please do not use rainbows or rainbow coloured font.

```html
<!DOCTYPE html>
<html lang="en">
<head>
<meta charset="utf-8">
<title>Bright Hearts Open Pages – My love card</title>
<link href="https://fonts.googleapis.com/css2?family=Nothing+You+Could+Do&family=Montserrat:wght@700&display=swap" rel="stylesheet">
<style>
  :root {
    --paper: #ffffff;
    --ink: #2a2a2a;
    --card-red: #be1e2d;
    --frame-taupe: #918379;
    --outline: #555555;
    --photo-dark: #3a3a3a;
    --photo-mid: #8c8c8c;
    --photo-light: #d2d2d2;
  }
  html, body {
    margin: 0;
    padding: 0;
    width: 804px;
    height: 1200px;
    overflow: hidden;
    background: var(--paper);
  }
  .canvas {
    position: relative;
    width: 804px;
    height: 1200px;
  }
  /* Outside of the card */
  .card-outside {
    position: absolute;
    left: 17px;
    top: 15px;
    width: 771px;
    height: 560px;
    border: 1px solid var(--outline);
    box-sizing: border-box;
    display: flex;
  }
  .back-cover {
    position: relative;
    width: 386px;
    height: 100%;
  }
  .brand-tag {
    position: absolute;
    left: 0;
    top: 0;
    width: 386px;
    height: 220px;
  }
  .brand-name {
    position: absolute;
    left: 160px;
    top: 100px;
    width: 98px;
    text-align: center;
    font-family: "Montserrat", sans-serif;
    font-weight: 700;
    font-size: 13px;
    line-height: 1.2;
    color: var(--paper);
  }
  .front-cover {
    position: relative;
    flex: 1;
    height: 100%;
  }
  .cover-photo {
    position: absolute;
    inset: 0;
    background: linear-gradient(160deg, var(--photo-dark) 0%, var(--photo-mid) 45%, var(--photo-light) 75%, var(--photo-mid) 100%);
  }
  .title-band {
    position: absolute;
    left: 0;
    top: 437px;
    width: 245px;
    height: 72px;
    background: var(--card-red);
    display: flex;
    align-items: center;
    justify-content: center;
  }
  .title {
    margin: 0;
    font-family: "Nothing You Could Do", cursive;
    font-weight: 400;
    font-size: 44px;
    color: var(--paper);
    line-height: 1;
    padding-top: 8px;
  }
  /* Inside of the card */
  .card-inside {
    position: absolute;
    left: 17px;
    top: 628px;
    width: 771px;
    height: 560px;
    background: var(--frame-taupe);
  }
  .inside-pages {
    position: absolute;
    left: 16px;
    top: 16px;
    width: 739px;
    height: 528px;
    background: var(--paper);
  }
  .fold-line {
    position: absolute;
    left: 387px;
    top: 0;
    width: 0;
    height: 560px;
    border-left: 1px dashed var(--outline);
  }
  .verse {
    position: absolute;
    left: 390px;
    top: 168px;
    width: 349px;
    margin: 0;
    text-align: center;
    font-family: "Nothing You Could Do", cursive;
    font-size: 22px;
    line-height: 48px;
    color: var(--ink);
  }
</style>
</head>
<body>
<div class="canvas">
  <section class="card-outside">
    <div class="back-cover">
      <svg class="brand-tag" viewBox="0 0 386 220" aria-hidden="true">
        <line x1="247" y1="0" x2="197" y2="78" stroke="var(--outline)" stroke-width="1"/>
        <circle cx="192" cy="123" r="62" fill="var(--card-red)"/>
        <circle cx="197" cy="78" r="3" fill="var(--paper)"/>
      </svg>
      <div class="brand-name">Bright Hearts Open Pages</div>
    </div>
    <div class="front-cover">
      <div class="cover-photo" role="img" aria-label="Black and white photograph of two men in shirts and ties embracing, one with his arm around the other"></div>
      <div class="title-band">
        <h1 class="title">My love...</h1>
      </div>
    </div>
  </section>

  <section class="card-inside">
    <div class="inside-pages"></div>
    <div class="fold-line"></div>
    <p class="verse">My heart stopped wandering<br>When it found home with you<br>I love you</p>
  </section>
</div>
</body>
</html>
```